Need a stunning home page for Car rental company

For a client, I need a slick and sumber home page design. It is a small, local car rental company, with a handful of cars available for rent.
Selling points: affordable lease, availability, always clean cars
The design should be:
- flat and modern
- no, or very few animations/sliders
- CTA: booking form for renting a car.
- 3 featured cars with images and facts (see website) with button to read more about the car.
- fullscreen background video can be an option
- main colour: #efba01
The site is under construction here:
http://solvikutleie.hammerlia.no/
Delivery requirements:
I need a layered & well organised PSD file delivered.

```html
<!DOCTYPE html>
<html lang="en">
<head>
<meta charset="utf-8">
<title>Solvikutleie – Car Rental</title>
<link href="https://fonts.googleapis.com/css2?family=Open+Sans:wght@400;600;700&display=swap" rel="stylesheet">
<style>
:root{
  --brand:#efba01;
  --nav:#6b6b6b;
  --dark:#3a3a3a;
  --text:#333;
  --muted:#777;
  --band:#e9e9e9;
  --footer:#575757;
  --footer-base:#444;
  --white:#fff;
}
*{margin:0;padding:0;box-sizing:border-box}
html,body{width:1200px;height:2200px;overflow:hidden}
body{font-family:"Open Sans",sans-serif;color:var(--text);background:var(--white);position:relative}
.abs{position:absolute}

/* header */
.site-header{position:absolute;left:0;top:0;width:1200px;height:110px;background:var(--white)}
.brand-name{left:100px;top:32px;font-size:34px;font-weight:700;color:var(--brand);letter-spacing:1px}
.hotline{left:550px;top:32px;font-size:16px;color:#888;line-height:21px}
.hotline-icon{left:696px;top:36px}
.utility{top:18px;font-size:12px;color:#555}
.search{left:858px;top:52px;width:242px;height:34px;background:#e6e6e6}
.search-btn{left:1068px;top:52px;width:32px;height:34px;background:var(--brand)}

/* nav */
.main-nav{position:absolute;left:0;top:110px;width:1200px;height:46px;background:var(--nav);display:flex;padding-left:100px}
.main-nav a{color:var(--white);text-decoration:none;font-size:13px;height:46px;line-height:46px;padding:0 34px;border-right:1px solid #7d7d7d}
.main-nav a.active{background:var(--brand);width:113px;text-align:center;padding:0}

/* hero */
.hero{left:0;top:156px;width:1200px;height:560px;background:linear-gradient(120deg,#4d5a4a 0%,#7a7d70 35%,#9aa19a 55%,#5e6b63 100%)}
.hero-play{left:546px;top:388px}
.dots{left:584px;top:692px;display:flex;gap:5px}
.dots i{width:7px;height:7px;border-radius:50%;background:#333;display:block}
.dots i.on{background:var(--brand)}
.booking{left:784px;top:246px;width:318px;height:380px;background:var(--brand);box-shadow:0 3px 8px rgba(0,0,0,.3);padding:18px 25px}
.booking h2{font-size:24px;font-weight:400;color:#333;text-align:center;margin-bottom:18px}
.booking label{display:block;font-size:13px;color:#333;margin-bottom:8px}
.field{height:32px;border:1px solid #555;font-size:12px;padding:7px 8px;color:#333;position:relative}
.row{display:flex;gap:22px;margin-top:18px}
.row>div{width:124px}
.book-btn{display:block;margin:30px auto 0;width:140px;height:34px;background:var(--dark);color:var(--white);font-size:13px;text-align:center;line-height:34px}

/* welcome */
.welcome{left:100px;top:756px;width:1000px;text-align:center}
.welcome h1{font-size:24px;font-weight:400;margin-bottom:18px}
.welcome p{font-size:12px;color:var(--muted);line-height:17px;margin:0 10px}
.btn-yellow{display:inline-block;background:var(--brand);font-size:12px;color:#333;padding:5px 18px;margin-top:30px}

/* featured */
.featured{left:0;top:960px;width:1200px;height:637px;background:var(--band)}
.section-title{width:1200px;text-align:center;font-size:24px;font-weight:400;color:#333}
.car-card{top:1033px;width:292px;height:514px;background:var(--white);box-shadow:0 2px 5px rgba(0,0,0,.2)}
.car-photo{height:201px}
.car-card h3{font-size:19px;font-weight:400;text-align:center;margin:14px 22px 0;padding-bottom:8px;border-bottom:1px solid #ddd}
.price{display:flex;justify-content:space-between;margin:0 22px;padding:12px 0;font-size:14px;border-bottom:1px solid #ddd}
.facts{margin:14px 22px 0;font-size:12px;line-height:22.5px}
.facts div{display:flex}
.facts span:first-child{width:182px}
.car-btn{position:absolute;left:0;bottom:0;width:292px;height:34px;background:var(--dark);color:var(--white);font-size:16px;text-align:center;line-height:34px}
.car-btn.primary{background:var(--brand);color:#333}

/* blog */
.blog-photo{top:1708px;width:322px;height:170px}
.blog-side{font-size:10px;line-height:13px;color:#555}
.blog-side b{display:block;color:#222;font-weight:600;font-size:11px;margin-bottom:8px}
.quote{left:948px;top:1708px;width:152px;height:170px;background:var(--brand);padding:12px 14px;font-size:10.5px;line-height:17px;color:#333}
.post-meta{top:1894px;width:300px}
.date{position:absolute;left:0;top:0;width:34px;text-align:center;font-size:9px;color:#888;line-height:11px}
.date b{display:block;font-size:16px;font-weight:400;color:#333;line-height:18px}
.post-body{position:absolute;left:45px;top:0;width:255px;border-left:1px solid #ddd;padding-left:10px;height:112px}
.post-body h4{font-size:13px;font-weight:400;color:#333}
.post-body .by{font-size:10px;color:#aaa;margin:3px 0 4px}
.post-body p{font-size:10px;color:#777;line-height:15px}
.post-body .more{font-size:10px;color:#333;margin-top:18px}
.arrow{color:#e05a3a}

/* footer */
.footer-nav{left:0;top:2103px;width:1200px;height:52px;background:var(--footer);text-align:center;line-height:52px;font-size:11px;font-weight:600;color:var(--white)}
.footer-nav span{margin:0 11px}
.footer-base{left:0;top:2155px;width:1200px;height:45px;background:var(--footer-base);color:var(--white);font-size:12px}
.social{left:1016px;top:2168px;display:flex;gap:8px}
.social i{display:block;width:20px;height:20px;border-radius:50%;background:var(--white)}
</style>
</head>
<body>

<header class="site-header">
  <div class="abs brand-name">SOLVIKUTLEIE</div>
  <div class="abs hotline">Question?<br>Call us 40 12 34 56</div>
  <svg class="abs hotline-icon" width="32" height="32" viewBox="0 0 32 32"><circle cx="16" cy="16" r="14" fill="none" stroke="#666" stroke-width="2"/><path d="M11 10c1-1 2-1 2.5 0l1.5 3c.3.6 0 1.2-.5 1.6l-1 .8c.8 1.8 2.2 3.2 4 4l.8-1c.4-.5 1-.8 1.6-.5l3 1.5c1 .5 1 1.5 0 2.5-1.5 1.5-4 1.3-7-1.2S9.5 11.5 11 10z" fill="#666"/></svg>
  <div class="abs utility" style="left:897px">Language: <svg width="16" height="11" style="vertical-align:-1px"><rect width="16" height="11" fill="#2a3f8f"/><path d="M0 5.5h16M8 0v11" stroke="#fff" stroke-width="3"/><path d="M0 5.5h16M8 0v11" stroke="#c22" stroke-width="1.5"/></svg> ▾</div>
  <div class="abs utility" style="left:1029px">My Account</div>
  <div class="abs search"></div>
  <div class="abs search-btn"><svg width="32" height="34"><circle cx="15" cy="16" r="4.5" fill="none" stroke="#333" stroke-width="1.5"/><path d="M18.5 19.5l3 3" stroke="#333" stroke-width="1.5"/></svg></div>
</header>

<nav class="main-nav">
  <a class="active">HOME</a>
  <a>THE FLEET OUR</a>
  <a>SERVICES</a>
  <a>CONTACT US</a>
  <a>BLOG</a>
  <a>PAGE TEMPLATES</a>
  <a style="border:0">ABOUT US</a>
</nav>

<section class="abs hero" role="img" aria-label="Couple driving a turquoise convertible along a tree-lined road"></section>
<svg class="abs hero-play" width="108" height="108" viewBox="0 0 108 108"><circle cx="54" cy="54" r="50" fill="none" stroke="#fff" stroke-width="5"/><path d="M44 34l30 20-30 20z" fill="#fff"/></svg>
<div class="abs dots"><i class="on"></i><i></i><i></i><i></i></div>

<form class="abs booking">
  <h2>Book a Car Now</h2>
  <label>Your Name</label>
  <div class="field">Jhon doe</div>
  <div class="row">
    <div><label>Car Name</label><div class="field">Voltra</div></div>
    <div><label>Model</label><div class="field">C100<span style="position:absolute;right:0;top:0;width:26px;height:30px;background:var(--dark);color:#fff;text-align:center;font-size:9px;line-height:30px">▼</span></div></div>
  </div>
  <div class="row">
    <div><label>From</label><div class="field">15-11-2014<span style="position:absolute;right:8px;top:8px;width:12px;height:12px;border:1px solid #555"></span></div></div>
    <div><label>To</label><div class="field"><span style="position:absolute;right:8px;top:8px;width:12px;height:12px;border:1px solid #555"></span></div></div>
  </div>
  <span class="abs" style="right:4px;top:252px;font-size:13px">to</span>
  <div class="book-btn">Book Now</div>
</form>

<section class="abs welcome">
  <h1>Welcome Solvik Car - Hammerlia</h1>
  <p>Solvik car is a fleet of Hammerlia and rent vans and cars for people who need a ekstrabil relocation, vacation, city tour or whatever. We beat the service, and most likely also the price. And you can trust that the car you get from us is both clean and pretty!V estibulum libero est, sodales sit amet magna congue, tempor fringilla augue. Etiam convallis pretium metus, eget hendrerit risus luctus id. Mauris commodo, lectus vel accumsan ultricies, orci massa molestie odio</p>
  <span class="btn-yellow">Read More</span>
</section>

<section class="abs featured"></section>
<h2 class="abs section-title" style="left:0;top:978px">Our Featured Cars</h2>

<article class="abs car-card" style="left:100px">
  <div class="car-photo" role="img" aria-label="White van parked by the sea at dusk" style="background:linear-gradient(180deg,#8a9cb0,#4a5560)"></div>
  <h3>Van</h3>
  <div class="price"><span>Price per day</span><span>kr 600</span></div>
  <div class="facts">
    <div><span>Biltyp to</span><span>Varebil</span></div>
    <div><span>Maks. pers.</span><span>2</span></div>
    <div><span>Ant. Doors</span><span>5</span></div>
    <div><span>Min. driver age</span><span>21</span></div>
    <div><span>Girtype</span><span>Manuell</span></div>
    <div><span>Klima Anlegg?</span><span>Well</span></div>
    <div><span>Unlimited km?</span><span>No</span></div>
  </div>
  <div class="car-btn primary">Read More About The Car ➔</div>
</article>

<article class="abs car-card" style="left:456px">
  <div class="car-photo" role="img" aria-label="Red hatchback on a seaside road" style="background:linear-gradient(160deg,#b8c0c4,#8a2a2e 55%,#3b3b3b)"></div>
  <h3>Car</h3>
  <div class="price"><span>Price per day</span><span>kr 600</span></div>
  <div class="facts">
    <div><span>Biltyp to</span><span>Varebil</span></div>
    <div><span>Maks. pers.</span><span>2</span></div>
    <div><span>Ant. Doors</span><span>5</span></div>
    <div><span>Min. driver age</span><span>21</span></div>
    <div><span>Girtype</span><span>Manuell</span></div>
    <div><span>Klima Anlegg?</span><span>Well</span></div>
    <div><span>Unlimited km?</span><span>No</span></div>
  </div>
  <div class="car-btn">Read More About The Car ➔</div>
</article>

<article class="abs car-card" style="left:810px">
  <div class="car-photo" role="img" aria-label="Silver sports car at a motor show" style="background:linear-gradient(180deg,#555,#c9c9cb 50%,#8c8c8e)"></div>
  <h3>Van</h3>
  <div class="price"><span>Price per day</span><span>kr 600</span></div>
  <div class="facts">
    <div><span>Biltyp to</span><span>Varebil</span></div>
    <div><span>Maks. pers.</span><span>2</span></div>
    <div><span>Ant. Doors</span><span>5</span></div>
    <div><span>Min. driver age</span><span>21</span></div>
    <div><span>Girtype</span><span>Manuell</span></div>
    <div><span>Klima Anlegg?</span><span>Well</span></div>
    <div><span>Unlimited km?</span><span>No</span></div>
  </div>
  <div class="car-btn">Read More About The Car ➔</div>
</article>

<h2 class="abs section-title" style="left:0;top:1643px">Our Blog</h2>
<svg class="abs" style="left:38px;top:1775px" width="22" height="36"><path d="M18 2L4 18l14 16" fill="none" stroke="#bbb" stroke-width="3"/></svg>
<svg class="abs" style="left:1140px;top:1775px" width="22" height="36"><path d="M4 2l14 16L4 34" fill="none" stroke="#bbb" stroke-width="3"/></svg>

<div class="abs blog-photo" style="left:101px;background:linear-gradient(120deg,#9aa0a6,#5f666c 60%,#c8b89a)" role="img" aria-label="Silver sedan driving at sunset"></div>
<div class="abs blog-side" style="left:438px;top:1708px;width:158px">
  <b>Dangers of home bed bug treatments</b>
  Sed ut perspiciatis unde omnis iste natus error sit voluptatem accusantium doloremque laudantium, totam rem aperiam.
</div>
<div class="abs blog-side" style="left:438px;top:1860px;font-size:10px;color:#222"><span class="arrow">➔</span> View all blog posts</div>

<div class="abs blog-photo" style="left:609px;background:radial-gradient(ellipse at 50% 60%,#3a3d42,#0c0f14 70%)" role="img" aria-label="Dark sports car front with headlights on"></div>
<aside class="abs quote">At vero eos et accusamus et iusto odio dignissimos ducimus qui blanditiis praesentium voluptatum deleniti atque corrupti quos dolores ete<div style="margin-top:14px;display:flex;justify-content:space-between"><span>Halvard Ness</span><span>»</span></div></aside>

<div class="abs post-meta" style="left:103px">
  <div class="date">FEB<b>08</b><div style="border-top:1px solid #ddd;margin-top:10px;padding-top:8px">♥<br>145</div></div>
  <div class="post-body">
    <h4>Dangers of home bed bug treatments</h4>
    <div class="by">Posted by Northpage | Street | 5 Comments</div>
    <p>Sed ut perspiciatis unde omnis iste natus error sit voluptatem accusantium doloremque laudantium, totam rem...</p>
    <div class="more"><span class="arrow">➔</span> Read more</div>
  </div>
</div>
<div class="abs post-meta" style="left:611px">
  <div class="date">FEB<b>08</b><div style="border-top:1px solid #ddd;margin-top:10px;padding-top:8px">♥<br>145</div></div>
  <div class="post-body">
    <h4>Dangers of home bed bug treatments</h4>
    <div class="by">Posted by Northpage | Street | 5 Comments</div>
    <p>Sed ut perspiciatis unde omnis iste natus error sit voluptatem accusantium doloremque laudantium, totam rem...</p>
    <div class="more"><span class="arrow">➔</span> Read more</div>
  </div>
</div>

<footer>
  <div class="abs footer-nav"><span>HOME</span>|<span>THE FLEET OUR</span>|<span>SERVICES</span>|<span>CONTACT US</span>|<span>BLOG</span>|<span>PAGE TEMPLATES</span>|<span>ABOUT US</span></div>
  <div class="abs footer-base"><span class="abs" style="left:101px;top:14px">Yoursite © 2014 All Rights Reserved.</span></div>
  <div class="abs social"><i></i><i></i><i></i></div>
</footer>

</body>
</html>
```